Enter the secret world of social tradecraft

Design a stunning work of art that markets our product "GreyLedger: A Hidden Casebook of Online Outreach Methods"

We need a set of assets for using in building our wordpress site and marketing materials. We'd like to have those assets delivered as a ONE PAGE HTML5 LANDING PAGE example.

We have a video that gives the look and feel of that we are going for and would like to extend it into a landing page for now with a customized logo to be included.

Watch the video here: https://www.vidcrate-example.net/clip/Tq7wLmZr2Pa

The product is an informational product containing information on QN marketing.

The final design should be intriguing and draw in the user with hints of intrigue.

Target Market(s)

Online Marketers

Industry/Entity Type

Marketing

Requirements
Must have
• Must match video in look and feel; must be html5 and responsive
Nice to have
• inventive html animations or css transitions

```html
<!DOCTYPE html>
<html lang="en">
<head>
<meta charset="utf-8">
<title>GreyLedger</title>
<link rel="stylesheet" href="https://fonts.googleapis.com/css2?family=Cinzel:wght@400;700&display=swap">
<style>
  :root {
    --ink: #000000;
    --bar: #050505;
    --bar-line: #222222;
    --menu-bg: #161616;
    --accent: #0033ff;
    --text: #ffffff;
    --mark: #d9d9d9;
    --frame: #3b3b3b;
    --screen: #0b080c;
    --play: rgba(200, 200, 200, 0.85);
  }
  * { margin: 0; padding: 0; box-sizing: border-box; }
  html, body {
    width: 1200px; height: 875px; overflow: hidden;
    background: var(--ink);
    font-family: "Cinzel", "Times New Roman", serif;
    color: var(--text);
  }
  .page { position: relative; width: 1200px; height: 875px; overflow: hidden; }

  .backdrop {
    position: absolute; inset: 55px 0 0 0;
    background:
      radial-gradient(ellipse 480px 300px at 600px 220px, #3a3a3a 0%, #1c1c1c 45%, transparent 80%),
      radial-gradient(ellipse 300px 260px at 1080px 150px, #262626 0%, transparent 75%),
      radial-gradient(ellipse 260px 240px at 120px 260px, #202020 0%, transparent 75%),
      linear-gradient(180deg, #141414 0%, #0a0a0a 55%, #000 85%);
  }

  .topbar {
    position: absolute; top: 0; left: 0; right: 0; height: 55px;
    background: var(--bar);
    border-bottom: 1px solid var(--bar-line);
  }
  .menu-toggle {
    position: absolute; left: 0; top: 0; width: 59px; height: 55px;
    background: var(--menu-bg);
    display: flex; flex-direction: column; justify-content: center; align-items: center; gap: 5px;
  }
  .menu-toggle span { display: block; width: 30px; height: 4px; background: var(--accent); }
  .site-name {
    position: absolute; left: 0; right: 0; top: 0; line-height: 55px;
    text-align: center; font-size: 30px; font-weight: 400; letter-spacing: 1px;
  }

  .brand-mark {
    position: absolute; left: 0; right: 0; top: 100px;
    text-align: center; color: var(--mark); font-weight: 400;
    text-shadow: none;
  }
  .brand-mark .line { display: block; font-size: 112px; line-height: 112px; letter-spacing: 8px; }

  .video {
    position: absolute; left: 384px; top: 425px; width: 440px; height: 266px;
    background: var(--frame); padding: 8px;
  }
  .video-screen {
    position: relative; width: 100%; height: 100%;
    background: radial-gradient(ellipse at 40% 40%, #1b1619 0%, var(--screen) 70%);
  }
  .video-screen svg { position: absolute; left: 0; top: 0; }

  .tagline {
    position: absolute; left: 0; right: 0; top: 716px;
    text-align: center; font-size: 34px; font-weight: 400; letter-spacing: 1px;
  }
  .cta {
    position: absolute; left: 479px; top: 776px; width: 250px; height: 45px;
    background: var(--accent); border-radius: 9px;
    color: var(--text); text-decoration: none; text-align: center;
    line-height: 45px; font-size: 21px; font-weight: 700; letter-spacing: 0.5px;
  }
  .legal {
    position: absolute; left: 0; right: 0; top: 843px;
    text-align: center; font-family: Arial, Helvetica, sans-serif; font-size: 12px;
  }
</style>
</head>
<body>
<div class="page">
  <div class="backdrop" role="img" aria-label="Dark smoky textured background with faint drafting lines"></div>

  <header class="topbar">
    <div class="menu-toggle" aria-label="Menu"><span></span><span></span><span></span></div>
    <h1 class="site-name">GREYLEDGER</h1>
  </header>

  <div class="brand-mark" aria-label="GreyLedger">
    <span class="line">GREY</span>
    <span class="line">LEDGER</span>
  </div>

  <div class="video">
    <div class="video-screen" role="img" aria-label="Intro video preview">
      <svg width="424" height="250" viewBox="0 0 424 250">
        <circle cx="212" cy="113" r="46" fill="var(--play)"/>
        <path d="M198 92 L231 113 L198 134 Z" fill="#111"/>
        <rect x="0" y="227" width="424" height="23" fill="#151515"/>
        <rect x="0" y="227" width="424" height="3" fill="#444"/>
        <rect x="0" y="227" width="95" height="3" fill="#cc1111"/>
        <rect x="9" y="236" width="3" height="8" fill="#bbb"/>
        <rect x="15" y="236" width="3" height="8" fill="#bbb"/>
        <path d="M30 238 H34 L38 235 V245 L34 242 H30 Z" fill="#bbb"/>
        <rect x="52" y="239" width="40" height="3" fill="#777"/>
        <circle cx="370" cy="240" r="3" fill="#999"/>
        <circle cx="385" cy="240" r="3" fill="#999"/>
        <rect x="396" y="237" width="8" height="6" fill="none" stroke="#999"/>
        <rect x="409" y="236" width="9" height="8" fill="none" stroke="#999"/>
      </svg>
    </div>
  </div>

  <h2 class="tagline">A HIDDEN CASEBOOK OF ONLINE OUTREACH METHODS</h2>
  <a class="cta" href="#">ENTER NOW</a>
  <p class="legal">Copyright © 2014 GreyLedger</p>
</div>
</body>
</html>
```